RVT Business Card Design

We are an independent auto dealer who specializes in commercial & fleet vehicles, we are family owned and operated and have been in business since 2001. We stock late model, low mileage, white trucks & vans. We mostly deal with companies in the construction and service industries. We are just looking to try to freshen up our old business card, we do not want to change the logo at this point, because it is well know within the southwest region & construction community. I have attached our logo and a PDF of our current business card for reference.
Updates
If the address is stacked there is no comma (,) after NE. Everyone keeps putting it in with this format and it is not correct.
482 Morrow Ave NE
Albuquerque, NM 87107
If the address is all on one line, then there will be a comma (,) after NE
482 Morrow Ave NE, Albuquerque, NM 87107
Please make changes accordingly, thank you for your attention in this matter.
Industry/Entity Type
Construction
Contact Information for Business Card
482 Morrow Ave NE, Albuquerque, NM 87107, Dorian Pellew, Vice President, dorian@rvtfleetcars.example, www.RVTfleetcars.example, ph 505-218-4470, fax 505-627-1904, cell 505-763-2085
Look and feel

```html
<!DOCTYPE html>
<html lang="en">
<head>
<meta charset="utf-8">
<title>RVT Auto Sales – Business Card</title>
<link rel="stylesheet" href="https://fonts.googleapis.com/css2?family=Open+Sans:wght@400;600;700&display=swap">
<style>
  :root {
    --page: #ececec;
    --card-light: #ffffff;
    --panel-dark-top: #454345;
    --panel-dark-bottom: #232224;
    --ink: #1d1d1f;
    --logo-ink: #3a3637;
    --accent-red: #ec2630;
    --panel-text: #cfcfcf;
    --muted: #5a5a5a;
  }
  * { box-sizing: border-box; margin: 0; padding: 0; }
  html, body {
    width: 1200px; height: 900px; overflow: hidden;
    background: var(--page);
    font-family: "Open Sans", Arial, sans-serif;
  }
  .stage {
    width: 1200px; height: 900px;
    display: flex; align-items: center; justify-content: center;
  }
  .business-card {
    width: 1000px; height: 572px;
    display: flex;
    box-shadow: 0 18px 40px rgba(0,0,0,0.22);
  }
  .card-front {
    width: 46%;
    background: var(--card-light);
    padding: 58px 0 0 52px;
    display: flex; flex-direction: column;
  }
  .brand {
    display: flex; flex-direction: column;
  }
  .brand-row { display: flex; align-items: center; gap: 14px; }
  .brand-mark {
    width: 22px; height: 22px; background: var(--accent-red);
  }
  .brand-name {
    font-size: 64px; font-weight: 700; color: var(--logo-ink);
    letter-spacing: 2px; line-height: 1;
  }
  .brand-sub {
    font-size: 40px; font-weight: 700; color: var(--logo-ink);
    letter-spacing: 3px; line-height: 1.1; margin-top: 6px;
  }
  .brand-rule {
    width: 330px; height: 3px; background: var(--logo-ink); margin-top: 10px;
  }
  .brand-tagline {
    font-size: 16px; color: var(--muted); margin-top: 12px; line-height: 1.35;
  }
  .online {
    margin-top: auto; margin-bottom: 70px;
    font-size: 29px; font-weight: 600; color: var(--ink); line-height: 1.3;
  }
  .card-back {
    width: 54%;
    background: linear-gradient(160deg, var(--panel-dark-top) 0%, var(--panel-dark-bottom) 100%);
    padding: 62px 40px 0 60px;
    color: var(--panel-text);
  }
  .person-name {
    font-size: 44px; font-weight: 600; color: var(--accent-red); line-height: 1.15;
  }
  .person-title {
    font-size: 38px; font-weight: 400; color: var(--panel-text);
    margin-left: 40px; line-height: 1.2;
  }
  .address {
    margin-top: 70px; font-size: 30px; font-weight: 600; line-height: 1.3;
  }
  .phones {
    margin-top: 18px;
    display: grid; grid-template-columns: 130px 30px auto;
    font-size: 30px; font-weight: 600; line-height: 1.3;
  }
</style>
</head>
<body>
<main class="stage">
  <article class="business-card">
    <section class="card-front">
      <div class="brand">
        <div class="brand-row">
          <span class="brand-name">RVT</span>
          <span class="brand-mark" aria-hidden="true"></span>
        </div>
        <span class="brand-sub">AUTO SALES</span>
        <span class="brand-rule" aria-hidden="true"></span>
        <p class="brand-tagline">Specializing in Commercial<br>&amp; Fleet Vehicles</p>
      </div>
      <div class="online">
        <p class="website">www.RVTfleetcars.example</p>
        <p class="email">dorian@rvtfleetcars.example</p>
      </div>
    </section>
    <section class="card-back">
      <h1 class="person-name">Dorian Pellew</h1>
      <p class="person-title">Vice President</p>
      <address class="address">482 Morrow Ave NE<br>Albuquerque, NM 87107</address>
      <div class="phones">
        <span>Phone</span><span>:</span><span>505-218-4470</span>
        <span>Cell</span><span>:</span><span>505-763-2085</span>
        <span>Fax</span><span>:</span><span>505-627-1904</span>
      </div>
    </section>
  </article>
</main>
</body>
</html>
```